Design a web site for my business - Brightline Coatings Co.

We are a family business that handles design, fabrication and installation of powder coated aluminum, stainless steel and glass products. Including handrails, privacy slat screens, electric gates and pool fencing. We are based in the Whitsundays in North Queensland and service an area from Airlie Beach to Townsville.

Target Market(s)

Domestic and commercial

Industry/Entity Type

fabrication - manufacturing

Coding

Coded - Design and coding required

Number of Pages Required

5+ page

Colors
0054AA
0677BA
7BADD7
CADEEF
E8F1F8

Requirements
Must have
• photo galleries, contact page, one page for privacy screens, balustrades, glass fencing, stainless steel handrail, powder coated aluminium handrails and pool fencing

```html
<!DOCTYPE html>
<html lang="en">
<head>
<meta charset="utf-8">
<title>Brightline Coatings Co — Aluminium, Glass & Stainless Steel Fabrication</title>
<link href="https://fonts.googleapis.com/css2?family=Inter:wght@400;500;600&family=Plus+Jakarta+Sans:wght@600;700&display=swap" rel="stylesheet">
<style>
:root{
  --blue:#0054AA; --blue-mid:#0677BA; --blue-soft:#7BADD7; --blue-pale:#CADEEF; --blue-wash:#E8F1F8;
  --ink:#0f1e36; --text:#3d5372; --navy:#0b1a33; --white:#fff; --line:#dfe8f2;
  --head:"Plus Jakarta Sans",sans-serif; --body:"Inter",sans-serif;
}
*{box-sizing:border-box;margin:0;padding:0}
html,body{width:1200px;height:4983px;overflow:hidden}
body{font-family:var(--body);color:var(--ink);background:var(--white)}
.wrap{width:962px;margin:0 auto;position:relative}
svg{display:block}
.eyebrow{font-size:10px;font-weight:600;letter-spacing:.12em;color:var(--blue);text-transform:uppercase}
h2{font-family:var(--head);font-weight:700;font-size:34px;line-height:1.15;color:var(--ink)}
.btn{display:inline-flex;align-items:center;gap:8px;height:38px;padding:0 22px;border-radius:20px;font-size:12px;font-weight:600;text-decoration:none}
.btn-solid{background:var(--blue);color:#fff}
.btn-ghost{border:1.5px solid var(--blue);color:var(--blue)}
.btn-glass{border:1px solid rgba(255,255,255,.5);color:#fff;background:rgba(255,255,255,.08)}

/* header + hero */
.hero{position:relative;height:623px;overflow:hidden;color:#fff}
.hero-photo{position:absolute;inset:0;background:linear-gradient(180deg,#3a5f86 0%,#2f5d80 35%,#1d4d7a 65%,#10407e 100%)}
.hero-shade{position:absolute;inset:0;background:linear-gradient(90deg,rgba(6,30,70,.55),rgba(6,30,70,.1))}
.nav{position:absolute;top:14px;left:119px;right:119px;height:34px;display:flex;align-items:center}
.brand{display:flex;align-items:center;gap:8px;font-family:var(--body);font-weight:600;font-size:12px;color:#fff;text-decoration:none}
.brand i{width:14px;height:14px;border-radius:50%;background:#fff;display:block}
.nav ul{list-style:none;display:flex;gap:30px;margin:0 auto;font-size:12px;padding-left:80px}
.nav ul a{color:#fff;text-decoration:none}
.nav .btn{height:30px;padding:0 16px;font-size:11px}
.hero-body{position:absolute;top:114px;left:119px;width:520px}
.pill{display:inline-block;border:1px solid rgba(255,255,255,.35);border-radius:12px;padding:4px 10px;font-size:9px;letter-spacing:.1em;font-weight:600;background:rgba(255,255,255,.08)}
.hero h1{font-family:var(--head);font-weight:700;font-size:44px;line-height:1.12;margin-top:18px}
.hero h1 span{color:var(--blue-soft)}
.hero p{font-size:13.5px;line-height:1.75;margin-top:18px;color:#e3edf7}
.hero .actions{display:flex;gap:14px;margin-top:26px}
.hero .actions .btn{height:36px;font-size:11px}
.tags{display:flex;gap:10px;margin-top:36px}
.tags span{display:flex;align-items:center;gap:6px;font-size:9.5px;border:1px solid rgba(255,255,255,.35);border-radius:12px;padding:5px 10px;background:rgba(255,255,255,.06);white-space:nowrap}
.trust{height:43px;background:var(--blue);color:#fff;font-size:11px}
.trust .wrap{display:flex;justify-content:space-between;align-items:center;height:43px}
.trust span{display:flex;align-items:center;gap:7px}

/* services */
.services{height:1033px;padding-top:104px}
.services .intro p{font-size:12.5px;line-height:1.7;color:var(--text);width:540px;margin-top:16px}
.services h2{margin-top:12px}
.cards{display:grid;grid-template-columns:repeat(3,308px);gap:19px;margin-top:46px}
.card{height:320px;border:1px solid var(--line);border-radius:6px;overflow:hidden;background:#fff}
.card .photo{height:166px}
.card .body{padding:20px 20px}
.card h3{font-family:var(--body);font-weight:600;font-size:13px}
.card p{font-size:11px;line-height:1.65;color:var(--blue-mid);margin-top:10px}
.more{display:flex;align-items:center;gap:6px;font-size:11px;font-weight:600;color:var(--blue);margin-top:16px}
.ph-water{background:linear-gradient(180deg,#6e9bc7 0%,#3f7fb0 55%,#2a5f86 100%)}
.ph-glass{background:linear-gradient(135deg,#2f4a36,#6d8a6d 50%,#9aa8a4)}
.ph-deck{background:linear-gradient(180deg,#3d4650,#5e5148 50%,#a39a8e)}
.ph-slat{background:linear-gradient(180deg,#6f8fb4,#9aa7b4 45%,#c9c3b4)}
.ph-sunset{background:linear-gradient(180deg,#1a2630 0%,#b9692a 50%,#e8a24a 58%,#2d2a2c 100%)}
.ph-walk{background:linear-gradient(160deg,#3f5c3c,#8a7a66 55%,#6e8b61)}

/* projects */
.projects{height:623px;background:#f4f8fc;padding-top:75px}
.projects .head{display:flex;justify-content:space-between;align-items:flex-end}
.projects h2{margin-top:12px}
.projects .btn{height:36px;font-size:11px;background:#fff}
.gallery{display:grid;grid-template-columns:312px 312px 312px;grid-template-rows:177px 177px;gap:12px 13px;margin-top:36px}
.gallery div{border-radius:4px}
.gallery .tall{grid-row:span 2}

/* why */
.why{height:716px;padding-top:118px}
.why .wrap{display:flex}
.why-photo{width:449px;height:465px;border-radius:6px;position:relative}
.badge{position:absolute;left:294px;top:408px;width:174px;height:76px;background:var(--blue);border-radius:8px;color:#fff;padding:18px 20px;box-shadow:0 8px 20px rgba(0,40,100,.3)}
.badge b{font-family:var(--head);font-size:22px;display:block;line-height:1}
.badge small{font-size:10px;color:var(--blue-pale)}
.why-text{margin-left:64px;padding-top:52px;width:449px}
.why-text h2{font-size:29px;margin-top:14px}
.why-text p{font-size:12px;line-height:1.75;color:var(--text);margin-top:20px}
.checks{display:grid;grid-template-columns:233px 200px;row-gap:11px;margin-top:24px;font-size:11px;font-weight:500}
.checks span{display:flex;align-items:center;gap:8px}
.why .actions{display:flex;gap:14px;margin-top:34px}
.why .btn{height:38px;font-size:11px}

/* testimonials */
.reviews{height:523px;background:var(--blue-wash);padding-top:105px;text-align:center}
.reviews h2{font-size:30px;margin-top:14px}
.quotes{display:grid;grid-template-columns:repeat(3,309px);gap:18px;margin-top:42px;text-align:left}
.quote{height:219px;background:#fff;border-radius:6px;padding:24px 24px;box-shadow:0 2px 10px rgba(0,60,120,.06)}
.stars{display:flex;gap:3px}
.quote p{font-size:11.5px;line-height:1.7;color:var(--ink);margin-top:16px;height:82px}
.who{display:flex;align-items:center;gap:12px;margin-top:22px}
.avatar{width:32px;height:32px;border-radius:50%;background:var(--blue-pale);color:var(--blue);display:flex;align-items:center;justify-content:center;font-size:11px;font-weight:600}
.who b{font-size:11px;font-weight:600;display:block}
.who small{font-size:9.5px;color:var(--blue-mid);display:flex;align-items:center;gap:3px;margin-top:2px}

/* coverage */
.coverage{height:551px;padding-top:87px}
.coverage .wrap{display:flex;justify-content:space-between}
.cov-text{width:450px;padding-top:25px}
.cov-text h2{font-size:30px;margin-top:12px}
.cov-text p{font-size:12px;line-height:1.7;color:var(--blue-mid);margin-top:20px}
.areas{display:grid;grid-template-columns:219px 219px;gap:11px 12px;margin-top:26px}
.areas span{height:36px;border:1px solid var(--blue-pale);border-radius:8px;display:flex;align-items:center;gap:10px;padding-left:14px;font-size:11px;font-weight:500;background:#fafcfe}
.map-area{width:447px;height:367px;border-radius:8px;background:linear-gradient(160deg,#e4ebe6 0%,#d9e6ee 100%);border:3px solid #fff;box-shadow:0 4px 16px rgba(0,60,120,.12)}

/* cta */
.cta{height:523px;position:relative;color:#fff;text-align:center;overflow:hidden}
.cta-photo{position:absolute;inset:0;background:linear-gradient(180deg,#14335f 0%,#1b477c 55%,#1f5a8e 100%)}
.cta-inner{position:relative;padding-top:132px}
.cta .eyebrow{color:var(--blue-pale)}
.cta h2{color:#fff;font-size:40px;line-height:1.22;margin-top:16px}
.cta p{font-size:13.5px;line-height:1.7;color:#dbe7f3;margin:22px auto 0;width:400px}
.cta .actions{display:flex;justify-content:center;gap:14px;margin-top:28px}
.cta .btn{height:40px;font-size:12px}

/* footer */
.footer{height:348px;background:var(--navy);color:#9fb2c9;padding-top:60px;font-size:11px}
.cols{display:flex}
.col-brand{width:250px}
.col-brand .brand{font-size:13px}
.col-brand p{line-height:1.7;margin-top:26px}
.socials{display:flex;gap:10px;margin-top:18px}
.socials i{width:22px;height:22px;border-radius:50%;border:1px solid #3c5474;display:block}
.col{font-size:10.5px}
.col h4{color:#fff;font-size:11px;font-weight:600;margin-bottom:16px}
.col li{list-style:none;margin-bottom:11px}
.col-links{margin-left:118px;width:247px}
.col-svc{width:250px}
.col-contact li{display:flex;gap:8px;align-items:flex-start}
.legal{border-top:1px solid #1e3150;margin-top:44px;padding-top:20px;display:flex;font-size:10px}
.legal span:first-child{margin-right:auto}
.legal span+span{margin-left:22px}
</style>
</head>
<body>

<header class="hero">
  <div class="hero-photo" role="img" aria-label="Waterfront beach houses with palm trees and a glass balustrade at dusk"></div>
  <div class="hero-shade"></div>
  <nav class="nav">
    <a class="brand" href="#"><i></i>Brightline Coatings Co</a>
    <ul><li><a href="#">Home</a></li><li><a href="#">About</a></li><li><a href="#">Services</a></li><li><a href="#">Gallery</a></li><li><a href="#">Projects</a></li><li><a href="#">Contact</a></li></ul>
    <a class="btn btn-solid" href="#">Request a Quote <svg width="10" height="10" viewBox="0 0 10 10"><path d="M1 5h8M5.5 1.5 9 5 5.5 8.5" stroke="#fff" stroke-width="1.4" fill="none"/></svg></a>
  </nav>
  <div class="hero-body">
    <span class="pill">+ WHITSUNDAYS &amp; NORTH QUEENSLAND</span>
    <h1>Premium Aluminium,<br>Glass &amp; Stainless<br><span>Steel Fabrication</span></h1>
    <p>Family-owned specialists delivering custom powder coated aluminium, stainless steel and glass solutions for residential and commercial projects across North Queensland.</p>
    <div class="actions">
      <a class="btn btn-solid" href="#">Get a Free Quote <svg width="10" height="10" viewBox="0 0 10 10"><path d="M1 5h8M5.5 1.5 9 5 5.5 8.5" stroke="#fff" stroke-width="1.4" fill="none"/></svg></a>
      <a class="btn btn-glass" href="#">View Our Projects <svg width="8" height="10" viewBox="0 0 8 10"><path d="M2 1.5 5.5 5 2 8.5" stroke="#fff" stroke-width="1.4" fill="none"/></svg></a>
    </div>
    <div class="tags">
      <span><svg width="10" height="10" viewBox="0 0 10 10"><circle cx="5" cy="5" r="4.3" stroke="#fff" fill="none"/><path d="M3 5.2 4.4 6.5 7 3.8" stroke="#fff" fill="none"/></svg>Family Owned</span>
      <span><svg width="10" height="10" viewBox="0 0 10 10"><circle cx="5" cy="5" r="4.3" stroke="#fff" fill="none"/><path d="M3 5.2 4.4 6.5 7 3.8" stroke="#fff" fill="none"/></svg>Custom Fabrication</span>
      <span><svg width="10" height="10" viewBox="0 0 10 10"><circle cx="5" cy="5" r="4.3" stroke="#fff" fill="none"/><path d="M3 5.2 4.4 6.5 7 3.8" stroke="#fff" fill="none"/></svg>Powder Coated Finish</span>
      <span><svg width="10" height="10" viewBox="0 0 10 10"><circle cx="5" cy="5" r="4.3" stroke="#fff" fill="none"/><path d="M3 5.2 4.4 6.5 7 3.8" stroke="#fff" fill="none"/></svg>Residential &amp; Commercial</span>
    </div>
  </div>
</header>

<div class="trust"><div class="wrap">
  <span><svg width="11" height="12" viewBox="0 0 11 12"><path d="M5.5 1 10 2.8v3.4c0 2.6-2 4.3-4.5 5-2.5-.7-4.5-2.4-4.5-5V2.8z" stroke="#fff" fill="none"/></svg>Australian Quality</span>
  <span><svg width="11" height="11" viewBox="0 0 11 11"><rect x="2" y="1" width="7" height="9" rx="1" stroke="#fff" fill="none"/><path d="M4 4h3M4 6.5h3" stroke="#fff"/></svg>Precision Manufacturing</span>
  <span><svg width="11" height="11" viewBox="0 0 11 11"><path d="M2 9 7 4M6.5 1.5a2.5 2.5 0 1 0 3 3" stroke="#fff" fill="none"/></svg>Expert Installation</span>
  <span><svg width="11" height="11" viewBox="0 0 11 11"><path d="M5.5 1 10 3.5 5.5 6 1 3.5zM1 6l4.5 2.5L10 6" stroke="#fff" fill="none"/></svg>Powder Coated Specialists</span>
  <span><svg width="10" height="12" viewBox="0 0 10 12"><path d="M5 11S1 7 1 4.5a4 4 0 0 1 8 0C9 7 5 11 5 11z" stroke="#fff" fill="none"/><circle cx="5" cy="4.5" r="1.4" stroke="#fff" fill="none"/></svg>Airlie Beach to Townsville</span>
</div></div>

<section class="services"><div class="wrap">
  <div class="intro">
    <div class="eyebrow">What we do</div>
    <h2>Our Services</h2>
    <p>From frameless glass to precision aluminium fabrication, every product is engineered to perform in Queensland's coastal climate and crafted to impress.</p>
  </div>
  <div class="cards">
    <article class="card"><div class="photo ph-water" role="img" aria-label="Powder coated handrail on a waterfront home"></div><div class="body"><h3>Powder Coated Aluminium Handrails</h3><p>Precision-engineered handrails with a durable powder coat finish — built for Queensland's coastal environment.</p><div class="more">Learn More <svg width="9" height="9" viewBox="0 0 10 10"><path d="M1 5h8M5.5 1.5 9 5 5.5 8.5" stroke="#0054AA" stroke-width="1.4" fill="none"/></svg></div></div></article>
    <article class="card"><div class="photo ph-glass" role="img" aria-label="Frameless glass pool fence beside tropical plants"></div><div class="body"><h3>Glass Pool Fencing</h3><p>Frameless and semi-frameless glass pool fencing with stainless steel spigots for a seamless, resort-style finish.</p><div class="more">Learn More <svg width="9" height="9" viewBox="0 0 10 10"><path d="M1 5h8M5.5 1.5 9 5 5.5 8.5" stroke="#0054AA" stroke-width="1.4" fill="none"/></svg></div></div></article>
    <article class="card"><div class="photo ph-deck" role="img" aria-label="Glass balustrade on an elevated timber deck"></div><div class="body"><h3>Glass Balustrades</h3><p>Architectural glass balustrade systems for elevated decks, balconies and luxury residential and commercial projects.</p><div class="more">Learn More <svg width="9" height="9" viewBox="0 0 10 10"><path d="M1 5h8M5.5 1.5 9 5 5.5 8.5" stroke="#0054AA" stroke-width="1.4" fill="none"/></svg></div></div></article>
    <article class="card"><div class="photo ph-slat" role="img" aria-label="Cream aluminium slat privacy screen"></div><div class="body"><h3>Privacy Slat Screens</h3><p>Powder coated aluminium louvre and slat systems delivering privacy, airflow and aesthetic appeal.</p><div class="more">Learn More <svg width="9" height="9" viewBox="0 0 10 10"><path d="M1 5h8M5.5 1.5 9 5 5.5 8.5" stroke="#0054AA" stroke-width="1.4" fill="none"/></svg></div></div></article>
    <article class="card"><div class="photo ph-sunset" role="img" aria-label="Sunset reflected through a glass balustrade"></div><div class="body"><h3>Electric Gates</h3><p>Custom fabricated automated gates with premium powder coat finishes for driveways and commercial entry points.</p><div class="more">Learn More <svg width="9" height="9" viewBox="0 0 10 10"><path d="M1 5h8M5.5 1.5 9 5 5.5 8.5" stroke="#0054AA" stroke-width="1.4" fill="none"/></svg></div></div></article>
    <article class="card"><div class="photo ph-walk" role="img" aria-label="Stainless steel handrail along a boardwalk"></div><div class="body"><h3>Stainless Steel Handrails</h3><p>Marine-grade stainless steel rod and cable handrail systems built to withstand the harshest coastal conditions.</p><div class="more">Learn More <svg width="9" height="9" viewBox="0 0 10 10"><path d="M1 5h8M5.5 1.5 9 5 5.5 8.5" stroke="#0054AA" stroke-width="1.4" fill="none"/></svg></div></div></article>
  </div>
</div></section>

<section class="projects"><div class="wrap">
  <div class="head">
    <div><div class="eyebrow">Portfolio</div><h2>Featured Projects</h2></div>
    <a class="btn btn-ghost" href="#">View Full Gallery <svg width="10" height="10" viewBox="0 0 10 10"><path d="M1 5h8M5.5 1.5 9 5 5.5 8.5" stroke="#0054AA" stroke-width="1.4" fill="none"/></svg></a>
  </div>
  <div class="gallery">
    <div class="tall ph-deck" role="img" aria-label="Elevated deck with glass balustrade"></div>
    <div class="ph-water" role="img" aria-label="Waterfront home with handrails"></div>
    <div class="ph-walk" role="img" aria-label="Boardwalk with stainless handrail"></div>
    <div class="ph-glass" role="img" aria-label="Glass pool fence among plants"></div>
    <div class="ph-slat" role="img" aria-label="Aluminium slat privacy screen"></div>
  </div>
</div></section>

<section class="why"><div class="wrap">
  <div class="why-photo ph-glass" role="img" aria-label="Frameless glass fence beside a garden path">
    <div class="badge"><b>10+</b><small>Years in the Whitsundays</small></div>
  </div>
  <div class="why-text">
    <div class="eyebrow">Why choose us</div>
    <h2>Crafted for the<br>Queensland Coast</h2>
    <p>We're a family business built on trust, quality materials, and genuine craftsmanship. Every project we undertake is engineered to withstand the harsh tropical environment while looking exceptional for decades to come.</p>
    <div class="checks">
      <span><svg width="12" height="12" viewBox="0 0 12 12"><circle cx="6" cy="6" r="5.2" stroke="#0054AA" fill="none"/><path d="M3.6 6.2 5.3 7.8 8.4 4.5" stroke="#0054AA" fill="none" stroke-width="1.2"/></svg>Family-Owned Business</span>
      <span><svg width="12" height="12" viewBox="0 0 12 12"><circle cx="6" cy="6" r="5.2" stroke="#0054AA" fill="none"/><path d="M3.6 6.2 5.3 7.8 8.4 4.5" stroke="#0054AA" fill="none" stroke-width="1.2"/></svg>Premium Powder Coating</span>
      <span><svg width="12" height="12" viewBox="0 0 12 12"><circle cx="6" cy="6" r="5.2" stroke="#0054AA" fill="none"/><path d="M3.6 6.2 5.3 7.8 8.4 4.5" stroke="#0054AA" fill="none" stroke-width="1.2"/></svg>Custom Design &amp; Fabrication</span>
      <span><svg width="12" height="12" viewBox="0 0 12 12"><circle cx="6" cy="6" r="5.2" stroke="#0054AA" fill="none"/><path d="M3.6 6.2 5.3 7.8 8.4 4.5" stroke="#0054AA" fill="none" stroke-width="1.2"/></svg>Expert Installation Team</span>
      <span><svg width="12" height="12" viewBox="0 0 12 12"><circle cx="6" cy="6" r="5.2" stroke="#0054AA" fill="none"/><path d="M3.6 6.2 5.3 7.8 8.4 4.5" stroke="#0054AA" fill="none" stroke-width="1.2"/></svg>Residential &amp; Commercial</span>
      <span><svg width="12" height="12" viewBox="0 0 12 12"><circle cx="6" cy="6" r="5.2" stroke="#0054AA" fill="none"/><path d="M3.6 6.2 5.3 7.8 8.4 4.5" stroke="#0054AA" fill="none" stroke-width="1.2"/></svg>Quality Materials Only</span>
      <span><svg width="12" height="12" viewBox="0 0 12 12"><circle cx="6" cy="6" r="5.2" stroke="#0054AA" fill="none"/><path d="M3.6 6.2 5.3 7.8 8.4 4.5" stroke="#0054AA" fill="none" stroke-width="1.2"/></svg>Coastal-Grade Finishes</span>
      <span><svg width="12" height="12" viewBox="0 0 12 12"><circle cx="6" cy="6" r="5.2" stroke="#0054AA" fill="none"/><path d="M3.6 6.2 5.3 7.8 8.4 4.5" stroke="#0054AA" fill="none" stroke-width="1.2"/></svg>Local Whitsundays Experts</span>
    </div>
    <div class="actions">
      <a class="btn btn-solid" href="#">Request a Quote <svg width="10" height="10" viewBox="0 0 10 10"><path d="M1 5h8M5.5 1.5 9 5 5.5 8.5" stroke="#fff" stroke-width="1.4" fill="none"/></svg></a>
      <a class="btn btn-ghost" href="#">Learn About Us <svg width="8" height="10" viewBox="0 0 8 10"><path d="M2 1.5 5.5 5 2 8.5" stroke="#0054AA" stroke-width="1.4" fill="none"/></svg></a>
    </div>
  </div>
</div></section>

<section class="reviews"><div class="wrap">
  <div class="eyebrow">Client stories</div>
  <h2>What Our Clients Say</h2>
  <div class="quotes">
    <article class="quote">
      <div class="stars"><svg width="76" height="12" viewBox="0 0 76 12"><g fill="#0677BA"><path id="st" d="M6 .5l1.6 3.6 3.9.4-2.9 2.6.8 3.9L6 9l-3.4 2 .8-3.9L.5 4.5l3.9-.4z"/><use href="#st" x="16"/><use href="#st" x="32"/><use href="#st" x="48"/><use href="#st" x="64"/></g></svg></div>
      <p>"Outstanding work on our beach house glass balustrades. The frameless panels are stunning and the finish is impeccable. Couldn't be happier."</p>
      <div class="who"><span class="avatar">D</span><div><b>Daniel &amp; Kate R.</b><small><svg width="7" height="9" viewBox="0 0 10 12"><path d="M5 11S1 7 1 4.5a4 4 0 0 1 8 0C9 7 5 11 5 11z" stroke="#0677BA" fill="none" stroke-width="1.4"/></svg>Airlie Beach</small></div></div>
    </article>
    <article class="quote">
      <div class="stars"><svg width="76" height="12" viewBox="0 0 76 12"><g fill="#0677BA"><use href="#st"/><use href="#st" x="16"/><use href="#st" x="32"/><use href="#st" x="48"/><use href="#st" x="64"/></g></svg></div>
      <p>"Brightline delivered custom privacy screens for our commercial project on time and on budget. The powder coat has held up perfectly in the coastal climate."</p>
      <div class="who"><span class="avatar">M</span><div><b>Marcus L.</b><small><svg width="7" height="9" viewBox="0 0 10 12"><path d="M5 11S1 7 1 4.5a4 4 0 0 1 8 0C9 7 5 11 5 11z" stroke="#0677BA" fill="none" stroke-width="1.4"/></svg>Bowen, QLD</small></div></div>
    </article>
    <article class="quote">
      <div class="stars"><svg width="76" height="12" viewBox="0 0 76 12"><g fill="#0677BA"><use href="#st"/><use href="#st" x="16"/><use href="#st" x="32"/><use href="#st" x="48"/><use href="#st" x="64"/></g></svg></div>
      <p>"Absolutely professional from start to finish. The stainless steel handrails on our pool deck are beautiful. A family business that takes real pride in their craft."</p>
      <div class="who"><span class="avatar">T</span><div><b>The Whitford Family</b><small><svg width="7" height="9" viewBox="0 0 10 12"><path d="M5 11S1 7 1 4.5a4 4 0 0 1 8 0C9 7 5 11 5 11z" stroke="#0677BA" fill="none" stroke-width="1.4"/></svg>Mackay, QLD</small></div></div>
    </article>
  </div>
</div></section>

<section class="coverage"><div class="wrap">
  <div class="cov-text">
    <div class="eyebrow">Coverage</div>
    <h2>Proudly Servicing<br>North Queensland</h2>
    <p>From the beach houses of Airlie Beach to commercial projects in Townsville — our team brings premium fabrication and powder coating expertise to every job site across the Whitsundays and North Queensland.</p>
    <div class="areas">
      <span><svg width="9" height="11" viewBox="0 0 10 12"><path d="M5 11S1 7 1 4.5a4 4 0 0 1 8 0C9 7 5 11 5 11z" stroke="#0054AA" fill="none" stroke-width="1.3"/><circle cx="5" cy="4.5" r="1.3" fill="#0054AA"/></svg>Airlie Beach</span>
      <span><svg width="9" height="11" viewBox="0 0 10 12"><path d="M5 11S1 7 1 4.5a4 4 0 0 1 8 0C9 7 5 11 5 11z" stroke="#0054AA" fill="none" stroke-width="1.3"/><circle cx="5" cy="4.5" r="1.3" fill="#0054AA"/></svg>Proserpine</span>
      <span><svg width="9" height="11" viewBox="0 0 10 12"><path d="M5 11S1 7 1 4.5a4 4 0 0 1 8 0C9 7 5 11 5 11z" stroke="#0054AA" fill="none" stroke-width="1.3"/><circle cx="5" cy="4.5" r="1.3" fill="#0054AA"/></svg>Bowen</span>
      <span><svg width="9" height="11" viewBox="0 0 10 12"><path d="M5 11S1 7 1 4.5a4 4 0 0 1 8 0C9 7 5 11 5 11z" stroke="#0054AA" fill="none" stroke-width="1.3"/><circle cx="5" cy="4.5" r="1.3" fill="#0054AA"/></svg>Mackay</span>
      <span><svg width="9" height="11" viewBox="0 0 10 12"><path d="M5 11S1 7 1 4.5a4 4 0 0 1 8 0C9 7 5 11 5 11z" stroke="#0054AA" fill="none" stroke-width="1.3"/><circle cx="5" cy="4.5" r="1.3" fill="#0054AA"/></svg>Townsville</span>
      <span><svg width="9" height="11" viewBox="0 0 10 12"><path d="M5 11S1 7 1 4.5a4 4 0 0 1 8 0C9 7 5 11 5 11z" stroke="#0054AA" fill="none" stroke-width="1.3"/><circle cx="5" cy="4.5" r="1.3" fill="#0054AA"/></svg>Whitsunday Islands</span>
    </div>
  </div>
  <div class="map-area" role="img" aria-label="Map of the service area around Airlie Beach"></div>
</div></section>

<section class="cta">
  <div class="cta-photo" role="img" aria-label="Hillside home with pool and glass fence overlooking the bay"></div>
  <div class="cta-inner">
    <div class="eyebrow">Get started today</div>
    <h2>Ready to Build Something<br>Exceptional?</h2>
    <p>Let's create custom aluminium, stainless steel and glass solutions tailored to your project.</p>
    <div class="actions">
      <a class="btn btn-solid" href="#">Request a Quote <svg width="10" height="10" viewBox="0 0 10 10"><path d="M1 5h8M5.5 1.5 9 5 5.5 8.5" stroke="#fff" stroke-width="1.4" fill="none"/></svg></a>
      <a class="btn btn-glass" href="#"><svg width="12" height="12" viewBox="0 0 12 12"><path d="M3 1 5 3.5 4 5a6 6 0 0 0 3 3l1.5-1L11 9l-1 2C5 11 1 7 1 2z" stroke="#fff" fill="none"/></svg>Call Now</a>
    </div>
  </div>
</section>

<footer class="footer"><div class="wrap">
  <div class="cols">
    <div class="col-brand">
      <a class="brand" href="#"><i></i>Brightline Coatings Co</a>
      <p>Premium aluminium fabrication and powder coating specialists serving the Whitsundays and North Queensland.</p>
      <div class="socials"><i></i><i></i><i></i></div>
    </div>
    <div class="col col-links"><h4>Quick Links</h4><ul><li>Home</li><li>About</li><li>Services</li><li>Gallery</li><li>Projects</li><li>Contact</li></ul></div>
    <div class="col col-svc"><h4>Services</h4><ul><li>Powder Coated Aluminium Handrails</li><li>Glass Pool Fencing</li><li>Glass Balustrades</li><li>Privacy Slat Screens</li><li>Electric Gates</li><li>Stainless Steel Handrails</li></ul></div>
    <div class="col col-contact"><h4>Contact</h4><ul>
      <li><svg width="9" height="11" viewBox="0 0 10 12"><path d="M5 11S1 7 1 4.5a4 4 0 0 1 8 0C9 7 5 11 5 11z" stroke="#7BADD7" fill="none" stroke-width="1.3"/></svg>Airlie Beach, QLD 4802 · Whitsundays, Australia</li>
      <li><svg width="10" height="10" viewBox="0 0 12 12"><path d="M3 1 5 3.5 4 5a6 6 0 0 0 3 3l1.5-1L11 9l-1 2C5 11 1 7 1 2z" stroke="#7BADD7" fill="none"/></svg>(07) 4900 0000</li>
      <li><svg width="11" height="9" viewBox="0 0 12 10"><rect x=".5" y=".5" width="11" height="9" rx="1" stroke="#7BADD7" fill="none"/><path d="M1 1l5 4 5-4" stroke="#7BADD7" fill="none"/></svg>hello@brightlinecoatings.com.au</li>
    </ul></div>
  </div>
  <div class="legal"><span>© 2025 Brightline Coatings Co. All rights reserved.</span><span>Privacy Policy</span><span>Terms of Service</span></div>
</div></footer>

</body>
</html>
```